Stylish Business Cards Wanted

- DOUBLE SIDED Design Required -

High end, edgy cards for a corporate and personal stylist. Must include logo,
Name: Belinda Harwick
Title: Director and Stylist
telephone : +61 8 7142 5809
email: belinda@theloombriefing.example
website: theloombriefing.example
Tag: Corporate Workwear & Uniform Specialist | Personal Stylist
Would like nice icons for telephone, email, website

Target Market(s)

Businesses wanting stylish uniforms, people wanting stylish wardrobes

Industry/Entity Type

Corporate Workwear Stylist

Contact Information for Business Card

I would like black, white and gold foiling incorporated in the design - possibly a touch of the other colours on my branding guide attached Name: Belinda Harwick Title: Director and Stylist telephone : +61 8 7142 5809 email: belinda@theloombriefing.example website: theloombriefing.example Tag: Corporate Workwear & Uniform Specialist | Personal Stylist Would like nice icons for telephone, email, website

Font styles to use
Other font styles liked:
• Raleway

Colors

Designer to choose colors to be used in the design.

Requirements
Must have
• Gold foil accents

```html
<!DOCTYPE html>
<html lang="en">
<head>
<meta charset="utf-8">
<title>The Loom Briefing — Business Cards</title>
<link rel="stylesheet" href="https://fonts.googleapis.com/css2?family=Arimo:wght@400;700&family=Montserrat:wght@500&family=Raleway:wght@600&display=swap">
<style>
  :root {
    --stage: #1d1d1d;
    --card-dark: #231f20;
    --card-light: #ffffff;
    --ink: #1a1718;
    --silver: #e9ecea;
    --gold: #e3b84b;
    --gold-light: #f2d272;
    --gold-deep: #d4a83c;
    --rule: #9a9a9a;
  }
  * { box-sizing: border-box; margin: 0; padding: 0; }
  html, body {
    width: 1200px;
    height: 1015px;
    overflow: hidden;
    background: var(--stage);
  }
  .sheet {
    width: 1200px;
    height: 1015px;
    display: flex;
    flex-direction: column;
    align-items: center;
    justify-content: center;
    gap: 48px;
  }
  .card {
    position: relative;
    width: 760px;
    height: 434px;
    overflow: hidden;
    box-shadow: 0 10px 30px rgba(0,0,0,.55);
  }
  .card--front { background: var(--card-dark); }
  .card--back { background: var(--card-light); }

  .gold-band {
    position: absolute;
    left: 0;
    right: 0;
    display: flex;
    align-items: center;
    justify-content: center;
    background: linear-gradient(100deg, var(--gold-deep), var(--gold-light) 45%, var(--gold) 70%, var(--gold-deep));
    font-family: "Arimo", Arial, sans-serif;
    color: var(--ink);
  }
  .card--front .gold-band {
    top: 262px;
    height: 74px;
    font-size: 21px;
    gap: 14px;
  }
  .card--back .gold-band {
    top: 320px;
    height: 62px;
    font-size: 20px;
    letter-spacing: 1px;
  }
  .separator-dot {
    width: 7px;
    height: 7px;
    border-radius: 50%;
    background: var(--ink);
  }

  .brand-name {
    position: absolute;
    left: 0;
    right: 0;
    text-align: center;
    font-family: "Raleway", sans-serif;
    font-weight: 600;
    letter-spacing: 2px;
  }
  .card--front .brand-name {
    top: 110px;
    font-size: 54px;
    color: var(--silver);
  }
  .card--back .brand-name {
    top: 40px;
    font-size: 40px;
    color: var(--ink);
  }

  .contact {
    position: absolute;
    top: 120px;
    left: 0;
    right: 0;
    display: flex;
    flex-direction: column;
    align-items: center;
    font-family: "Arimo", Arial, sans-serif;
    color: var(--ink);
  }
  .contact__name {
    font-family: "Montserrat", sans-serif;
    font-weight: 500;
    font-size: 28px;
    color: var(--gold);
    letter-spacing: 1px;
  }
  .contact__title { font-size: 20px; margin-top: 2px; }
  .contact__rule {
    width: 190px;
    height: 1px;
    background: var(--rule);
    margin: 12px 0 14px;
  }
  .contact__line { font-size: 20px; line-height: 1.35; }
</style>
</head>
<body>
  <main class="sheet">
    <section class="card card--front" aria-label="Business card front">
      <p class="brand-name">The Loom Briefing</p>
      <div class="gold-band">
        <span>Corporate Workwear &amp; Uniform Specialist</span>
        <span class="separator-dot"></span>
        <span>Personal Stylist</span>
      </div>
    </section>

    <section class="card card--back" aria-label="Business card back">
      <p class="brand-name">The Loom Briefing</p>
      <div class="contact">
        <p class="contact__name">BELINDA HARWICK</p>
        <p class="contact__title">Director and Stylist</p>
        <span class="contact__rule"></span>
        <p class="contact__line">+61 8 7142 5809</p>
        <p class="contact__line">belinda@theloombriefing.example</p>
      </div>
      <div class="gold-band">
        <span>WWW.THELOOMBRIEFING.EXAMPLE</span>
      </div>
    </section>
  </main>
</body>
</html>
```